TRV Letterhead Design Project

Design a new company letterhead utilizing our new logo and color scheme. Interested in professional letterhead and matching 2nd sheet versions.
Updates

I have uploaded windows format files now.  Originally only uploaded MAC file format.  Good luck!

Target Market(s)

Industry Executives, construction managers, well educated and discriminate personnel. Project needs to leave an impression and have impact but not be cluttered, busy or too in your face.

Industry/Entity Type

It Company

Requirements
Must have
• Clean, crisp look, true to new logo and color scheme, professional image. Should include spaces for company web address, address info and phone & fax numbers

```html
<!DOCTYPE html>
<html lang="en">
<head>
<meta charset="utf-8">
<title>TRV Letterhead</title>
<link rel="stylesheet" href="https://fonts.googleapis.com/css2?family=Open+Sans:wght@400;600&display=swap">
<style>
  :root {
    --brand-orange: #e07b1f;
    --brand-grey: #58595b;
    --text-dark: #2b2b2b;
    --watermark-grey: #e6e6e7;
    --backdrop: #ece8e3;
    --paper: #ffffff;
  }
  * { box-sizing: border-box; margin: 0; padding: 0; }
  html, body {
    width: 1200px; height: 1071px; overflow: hidden;
    background: var(--backdrop);
    font-family: "Open Sans", Arial, sans-serif;
    color: var(--text-dark);
  }
  .letterhead {
    position: absolute; left: 233px; top: 48px;
    width: 685px; height: 969px;
    background: var(--paper);
    overflow: hidden;
    box-shadow: 0 2px 6px rgba(0,0,0,.25);
  }
  .watermark {
    position: absolute; left: 410px; top: 540px;
    width: 330px; height: 330px; border-radius: 50%;
    background: var(--watermark-grey);
    opacity: .85;
  }
  .brand {
    position: absolute; left: 75px; top: 70px; width: 246px;
    text-align: center;
  }
  .brand-mark {
    width: 84px; height: 84px; margin: 0 auto 12px;
    border-radius: 50%; background: var(--brand-grey);
  }
  .brand-name {
    font-size: 40px; font-weight: 600; letter-spacing: 4px;
    color: var(--brand-orange); line-height: 1;
  }
  .contact {
    position: absolute; left: 477px; top: 68px;
    font-size: 12.5px; line-height: 18.5px; color: var(--text-dark);
    list-style: none;
  }
  .contact .address { margin-bottom: 8px; line-height: 16px; }
  .contact li { display: flex; align-items: center; gap: 6px; }
  .contact svg { width: 10px; height: 10px; fill: var(--brand-orange); flex: none; }
  .accent-bar {
    position: absolute; right: 0; top: 71px;
    width: 16px; height: 111px; background: var(--brand-orange);
  }
  .letter {
    position: absolute; left: 64px; top: 342px; width: 551px;
  }
  .salutation { font-size: 19px; font-weight: 600; margin-bottom: 4px; }
  .body-copy {
    font-size: 14.6px; line-height: 20px; text-align: justify;
  }
  .signature {
    width: 160px; height: 44px; margin: 30px 0 0 6px;
    border-bottom: 1.5px solid var(--text-dark); opacity: .6;
  }
  .signatory { font-size: 11.5px; margin-top: 16px; }
</style>
</head>
<body>
  <main class="letterhead">
    <div class="watermark" aria-hidden="true"></div>

    <header class="brand">
      <div class="brand-mark" aria-hidden="true"></div>
      <div class="brand-name">TRV</div>
    </header>

    <ul class="contact">
      <li class="address">Your location address info<br>go in here</li>
      <li><svg viewBox="0 0 10 10"><path d="M1 3h8v5H1z M2 1h6l1 2H1z"/></svg>+100 555 0142 8870</li>
      <li><svg viewBox="0 0 10 10"><path d="M2 1h6v3H2z M1 4h8v5H1z"/></svg>+100 555 0142 8871</li>
      <li><svg viewBox="0 0 10 10"><path d="M1 2h8v6H1z"/></svg>info@trvgroup.example</li>
      <li><svg viewBox="0 0 10 10"><circle cx="5" cy="5" r="4.5"/></svg>www.trvgroup.example</li>
    </ul>
    <div class="accent-bar" aria-hidden="true"></div>

    <article class="letter">
      <p class="salutation">Dear sir,</p>
      <p class="body-copy">Lorem Ipsum. Proin gravida nibh vel velit auctor aliquet. Aenean sollicitudin, lorem quis bibendum auctor, nisi elit consequat ipsum, nec sagittis sem nibh id elit. Duis sed odio sit amet nibh vulputate cursus a sit amet mauris. Morbi accumsan ipsum velit. Nam nec tellus a odio tincidunt auctor a ornare odio. Sed non mauris vitae erat consequat auctor eu in elit. Class aptent taciti sociosqu ad litora torquent per conubia nostra, per inceptos himenaeos. Mauris in erat justo. Nullam ac urna eu felis dapibus condimentum sit amet a augue. Sed non neque elit. Sed ut imperdiet nisi. Proin condimentum fermentum nunc. Etiam pharetra, erat sed fermentum feugiat, velit mauris egestas quam, ut aliquam massa nisl quis neque. Suspendisse in orci enim. Class aptent taciti sociosqu ad litora torquent per conubia nostra, per inceptos himenaeos. Mauris in erat justo. Nullam ac urna eu felis dapibus condimentum sit amet a augue. Sed non neque elit. Sed ut imperdiet nisi. Proin condimentum fermentum nunc. Sed non mauris vitae erat consequat auctor eu in elit. Class aptent taciti sociosqu ad litora torquent per conubia nostra, per inceptos himenaeos. Mauris in erat justo.</p>
      <div class="signature" role="img" aria-label="Handwritten signature of the signatory"></div>
      <p class="signatory">Nora Vale, Co-Founder &amp; CEO</p>
    </article>
  </main>
</body>
</html>
```